Creation of an elegant and modern turnkey Shopify website

Hello,

We are a new company specializing in the sale of above-ground pools. We want to create a turnkey website, ideally using Shopify. For now, we need a "showcase" site, not an e-commerce platform, with four tabs:

Home Page (an overall presentation of the company)
Our Products (an overview of all the above-ground pools we sell)
Our Projects (a page inspired by Instagram to showcase photos of our future projects)
Contact (a page with all our contact information and a contact form)

We are looking to create a highly visual, elegant, and modern website with vibrant splashes of color. We will provide the text, photos (along with instructions on where to place them on each page), and all other necessary information as attachments.

Thank you in advance for your proposals!

The Brisa Lagoon Team

Target Market(s)

Targeted at Swiss customers (a translator will need to be installed for different languages)

Industry/Entity Type

Sale of customised above-ground pools

Coding

Coded - Design and coding required

Font styles to use
Sans Serif

Colors
0094D4
00A9DD
6FCCEA
C7EBF8
E9F6FB
00AB8E
00BBA5
67D7C9
C6EFE9
E9F9F6

Requirements
Must have
• A stunning, elegant and modern look
Nice to have
• Inspiration from the colors of our logo throughout the site, but in an elegant way
Should not have
• An overly classic look for swimming pool sites

```html
<!DOCTYPE html>
<html lang="en">
<head>
<meta charset="utf-8">
<title>Brisa Lagoon – Above-Ground Pools</title>
<link rel="stylesheet" href="https://fonts.googleapis.com/css2?family=Plus+Jakarta+Sans:wght@300;400;500;600&display=swap">
<style>
:root{
  --cyan:#00c3d9;
  --cyan-text:#1cb8cf;
  --header:#bdf3fb;
  --panel:#effcfd;
  --ink:#2d3436;
  --white:#ffffff;
  --photo-slate:#66737a;
  --photo-aqua:#a6e4ee;
  --photo-pale:#bdeef5;
  --photo-teal:#2fbfc0;
  --photo-blue:#5cbfe0;
  --photo-light:#e4e4e4;
  --photo-taupe:#bdb6ad;
  --photo-dark:#27323a;
}
*{box-sizing:border-box;margin:0;padding:0}
html,body{width:1200px;height:4762px;overflow:hidden}
body{position:relative;background:var(--white);font-family:"Plus Jakarta Sans",sans-serif;color:var(--ink)}
.photo{position:absolute}
.panel{position:absolute;background:var(--panel)}
.btn{position:absolute;display:flex;align-items:center;justify-content:center;gap:10px;background:var(--cyan);color:var(--white);font-size:16px;font-weight:500;letter-spacing:.2px}
.btn svg{width:10px;height:14px}
.rule{position:absolute;height:6px;background:var(--cyan)}

/* header */
.site-header{position:absolute;left:0;top:0;width:1200px;height:78px;background:var(--header)}
.brand-small{position:absolute;left:76px;top:25px;font-size:22px;font-weight:300;color:var(--cyan-text);letter-spacing:1px}
.nav{position:absolute;left:395px;top:30px;display:flex;gap:21px;font-size:13px;font-weight:500;color:var(--ink)}
.nav span{padding-bottom:9px}
.nav .active{border-bottom:2px solid var(--ink);padding:0 6px 9px}
.lang{position:absolute;left:1044px;top:28px;display:flex;align-items:center;gap:8px;font-size:13px;font-weight:500}
.lang i{display:block;width:18px;height:18px;border-radius:50%;background:#c9364b}

/* hero */
.slider-arrow{position:absolute;width:36px;height:36px;background:rgba(255,255,255,.45);display:flex;align-items:center;justify-content:center}
.dots{position:absolute;left:350px;top:681px;display:flex;gap:10px}
.dots i{width:8px;height:8px;border-radius:50%;background:rgba(255,255,255,.6)}
.dots i:first-child{background:var(--white)}
.welcome{position:absolute;left:0;top:82px;width:434px;text-align:center;font-size:30px;font-weight:400;color:var(--ink)}
.brand-large{position:absolute;left:0;top:142px;width:434px;text-align:center;font-size:76px;line-height:84px;font-weight:300;color:var(--cyan-text);letter-spacing:4px}
.tagline{position:absolute;left:0;top:380px;width:434px;text-align:center;font-size:16px;line-height:29px}

/* dream */
.dream-title{position:absolute;left:67px;width:432px;top:817px;text-align:center;font-size:42px;line-height:58px;font-weight:500;color:var(--cyan-text)}
.dream-text{position:absolute;left:67px;width:432px;top:1104px;text-align:center;font-size:16px;line-height:29px}

/* banner */
.banner-box{position:absolute;left:166px;top:1396px;width:866px;height:361px;background:rgba(239,252,253,.6)}
.banner-title{position:absolute;left:0;width:1200px;top:1436px;text-align:center;font-size:40px;font-weight:500;color:var(--ink)}
.banner-text{position:absolute;left:236px;width:728px;top:1540px;text-align:center;font-size:16px;line-height:29px}

/* features */
.section-heading{position:absolute;font-size:42px;line-height:57px;font-weight:600;color:var(--cyan-text)}
.bar{position:absolute;width:3px;background:var(--cyan)}
.feature{position:absolute}
.feature h3{font-size:29px;font-weight:500;color:var(--cyan-text);line-height:40px}
.feature p{font-size:16px;line-height:29px;margin-top:8px}

/* faq */
.faq-item{position:absolute;left:100px;width:1000px;border:3px solid var(--cyan);background:var(--white)}
.faq-q{display:flex;justify-content:space-between;align-items:center;padding:0 16px;height:59px;font-size:23px;color:var(--cyan-text);font-weight:400}
.faq-a{padding:0 16px;font-size:16px;line-height:29px;margin-top:-4px}

/* cards */
.dreams-band{position:absolute;left:67px;top:3724px;width:1066px;height:89px;background:var(--panel);display:flex;align-items:center;justify-content:center;font-size:38px;font-weight:500;color:var(--cyan-text)}
.card{position:absolute;top:3826px;width:343px;height:527px;background:var(--panel)}
.card .photo{left:0;top:0;width:343px;height:264px}
.card h4{position:absolute;left:16px;top:296px;font-size:23px;line-height:33px;font-weight:500;color:var(--ink)}
.card .rule{left:16px;top:368px;width:311px;height:3px}
.card p{position:absolute;left:16px;top:388px;width:300px;font-size:15.5px;line-height:29px}

/* footer */
.site-footer{position:absolute;left:0;top:4371px;width:1200px;height:391px;background:var(--header)}
.brand-footer{position:absolute;left:105px;top:60px;font-size:54px;line-height:68px;font-weight:300;color:var(--cyan-text);letter-spacing:3px}
.social{position:absolute;left:115px;top:252px;display:flex;gap:18px}
.social i{display:block;width:26px;height:26px;background:var(--ink);border-radius:3px}
.footer-col{position:absolute;top:57px;font-size:16px;line-height:29px}
.footer-col h5{font-size:23px;line-height:30px;font-weight:500;margin-bottom:16px}
.sub-form{display:flex;margin-top:12px}
.sub-form span{width:249px;height:41px;background:var(--white);font-size:12px;color:#999;padding:11px 10px;border:1px solid #e4f3f5}
.sub-form b{width:84px;height:41px;background:var(--cyan);color:var(--white);font-size:13px;font-weight:500;display:flex;align-items:center;justify-content:center;margin-left:2px}
.footer-rule{position:absolute;left:67px;top:313px;width:1066px;height:3px;background:#0aa0d8}
.copyright{position:absolute;left:67px;top:332px;font-size:10px}
</style>
</head>
<body>

<header class="site-header">
  <div class="brand-small">BRISA LAGOON</div>
  <nav class="nav"><span class="active">HOME</span><span>OUR PRODUCTS</span><span>OUR PROJECTS</span><span>CONTACT</span></nav>
  <div class="lang"><i></i>ENG
    <svg width="14" height="8" viewBox="0 0 14 8"><path d="M0 0h14L7 8z" fill="#2d3436"/></svg></div>
</header>

<!-- hero -->
<div class="photo" role="img" aria-label="Photo: above-ground pool with slatted cladding in a garden" style="left:67px;top:111px;width:613px;height:599px;background:var(--photo-slate)"></div>
<div class="slider-arrow" style="left:82px;top:392px"><svg width="10" height="14" viewBox="0 0 10 14"><path d="M8 1L2 7l6 6" stroke="#fff" stroke-width="2" fill="none"/></svg></div>
<div class="slider-arrow" style="left:632px;top:392px"><svg width="10" height="14" viewBox="0 0 10 14"><path d="M2 1l6 6-6 6" stroke="#fff" stroke-width="2" fill="none"/></svg></div>
<div class="dots"><i></i><i></i><i></i></div>

<section class="panel" style="left:699px;top:111px;width:434px;height:599px">
  <div class="welcome">Welcome To</div>
  <div class="brand-large">BRISA<br>LAGOON</div>
  <div class="rule" style="left:117px;top:346px;width:200px"></div>
  <div class="tagline">Transform Your Garden with Our Premium<br>Above-Ground Pools!</div>
  <div class="btn" style="left:33px;top:468px;width:368px;height:44px">CONTACT US <svg viewBox="0 0 10 14"><path d="M2 1l6 6-6 6" stroke="#fff" stroke-width="2" fill="none"/></svg></div>
</section>

<!-- dream -->
<section class="panel" style="left:67px;top:728px;width:432px;height:598px"></section>
<div class="dream-title">Have You Ever<br>Dreamt of<br>Relaxing in The<br>Middle of A Pool?</div>
<div class="rule" style="left:183px;top:1073px;width:200px"></div>
<div class="dream-text">Achieve your dreams with our custom, tailor-<br>made above-ground pools.</div>
<div class="btn" style="left:100px;top:1193px;width:368px;height:44px">CONTACT US <svg viewBox="0 0 10 14"><path d="M2 1l6 6-6 6" stroke="#fff" stroke-width="2" fill="none"/></svg></div>
<div class="photo" role="img" aria-label="Photo: aerial view of a person relaxing on a float in a pool" style="left:518px;top:728px;width:615px;height:598px;background:var(--photo-aqua)"></div>

<!-- banner -->
<div class="photo" role="img" aria-label="Photo: clear pool water" style="left:67px;top:1344px;width:1066px;height:464px;background:var(--photo-pale)"></div>
<div class="banner-box"></div>
<h2 class="banner-title">BRING HAPPINESS THROUGH CHANGE</h2>
<div class="rule" style="left:433px;top:1508px;width:334px;height:5px"></div>
<p class="banner-text">Imagine an exceptional relaxation and leisure space right in your own backyard. With our unparalleled expertise and commitment to excellence, we create above-ground pools that exceed all expectations. Our exclusive, custom-designed models are crafted to combine style, durability, and innovation, offering a unique and refined experience.</p>
<div class="btn" style="left:292px;top:1679px;width:300px;height:46px">CONTACT US <svg viewBox="0 0 10 14"><path d="M2 1l6 6-6 6" stroke="#fff" stroke-width="2" fill="none"/></svg></div>
<div class="btn" style="left:608px;top:1679px;width:300px;height:46px">LEARN MORE <svg viewBox="0 0 10 14"><path d="M2 1l6 6-6 6" stroke="#fff" stroke-width="2" fill="none"/></svg></div>

<!-- why choose -->
<section class="panel" style="left:67px;top:1827px;width:523px;height:599px"></section>
<div class="bar" style="left:89px;top:1886px;height:176px"></div>
<h2 class="section-heading" style="left:124px;top:1889px">WHY CHOOSE OUR<br>ABOVE-GROUND<br>POOLS?</h2>
<div class="bar" style="left:93px;top:2094px;height:110px"></div>
<div class="feature" style="left:113px;top:2095px;width:460px"><h3>Superior Quality</h3><p>Each pool is constructed with high-quality materials,<br>ensuring exceptional durability and strength.</p></div>
<div class="bar" style="left:93px;top:2234px;height:106px"></div>
<div class="feature" style="left:113px;top:2234px;width:460px"><h3>Elegant Design</h3><p>Our pools come in a variety of styles and finishes,<br>seamlessly blending into any garden setting.</p></div>
<div class="photo" role="img" aria-label="Photo: top view of a long pool with a swimmer" style="left:608px;top:1827px;width:525px;height:599px;background:var(--photo-teal)"></div>

<!-- and also -->
<div class="photo" role="img" aria-label="Photo: aerial view of a woman in a sun hat beside a pool" style="left:67px;top:2444px;width:523px;height:598px;background:var(--photo-blue)"></div>
<section class="panel" style="left:608px;top:2444px;width:525px;height:598px"></section>
<div class="bar" style="left:633px;top:2500px;height:58px"></div>
<h2 class="section-heading" style="left:666px;top:2500px">AND ALSO...</h2>
<div class="bar" style="left:636px;top:2586px;height:114px"></div>
<div class="feature" style="left:656px;top:2587px;width:470px"><h3>Custom and Tailor-Made</h3><p>Create the pool of your dreams with our customization<br>options, tailored to your specific tastes and needs.</p></div>
<div class="bar" style="left:636px;top:2731px;height:114px"></div>
<div class="feature" style="left:656px;top:2733px;width:470px"><h3>Easy Installation</h3><p>Enjoy your new oasis quickly with our simple and fast<br>installation process.</p></div>
<div class="bar" style="left:636px;top:2875px;height:114px"></div>
<div class="feature" style="left:656px;top:2877px;width:470px"><h3>Constant Innovation</h3><p>We incorporate the latest technologies to provide you<br>with an optimal and safe swimming experience.</p></div>

<!-- faq -->
<section class="panel" style="left:67px;top:3060px;width:1066px;height:646px"></section>
<div class="bar" style="left:96px;top:3115px;height:58px"></div>
<h2 class="section-heading" style="left:129px;top:3115px;font-size:40px">FREQUENTLY ASK QUESTIONS</h2>
<div class="faq-item" style="top:3206px;height:169px">
  <div class="faq-q">What is Brisa Lagoon?<svg width="20" height="2" viewBox="0 0 20 2"><rect width="20" height="2" fill="#1cb8cf"/></svg></div>
  <p class="faq-a">Lorem ipsum dolor sit amet consectetur. Amet nec lacus aenean non. Semper volutpat pellentesque facilisis molestie. Sit cras suspendisse vel blandit pellentesque cursus. Dictum non amet urna in tortor nullam. Malesuada odio ultricies tristique egestas mauris egestas est elementum malesuada. Tristique turpis dignissim eu suspendisse velit ornare felis. In cursus.</p>
</div>
<div class="faq-item" style="top:3393px;height:65px"><div class="faq-q">Why choose Brisa Lagoon?<svg width="20" height="20" viewBox="0 0 20 20"><path d="M10 0v20M0 10h20" stroke="#1cb8cf" stroke-width="2"/></svg></div></div>
<div class="faq-item" style="top:3476px;height:65px"><div class="faq-q">How to consult with Brisa Lagoon?<svg width="20" height="20" viewBox="0 0 20 20"><path d="M10 0v20M0 10h20" stroke="#1cb8cf" stroke-width="2"/></svg></div></div>
<div class="faq-item" style="top:3559px;height:65px"><div class="faq-q">What are the benefits?<svg width="20" height="20" viewBox="0 0 20 20"><path d="M10 0v20M0 10h20" stroke="#1cb8cf" stroke-width="2"/></svg></div></div>

<!-- dreams -->
<h2 class="dreams-band">WE BRING YOUR POOL DREAMS TO LIFE!</h2>
<article class="card" style="left:67px">
  <div class="photo" role="img" aria-label="Photo: consultant holding a tablet" style="background:var(--photo-light)"></div>
  <h4>PERSONALIZED<br>SERVICES</h4><div class="rule"></div>
  <p>We understand that every garden and client is unique. That's why we offer personalized services, from design to installation and after-sales support.</p>
</article>
<article class="card" style="left:427px">
  <div class="photo" role="img" aria-label="Photo: document being stamped on a desk" style="background:var(--photo-taupe)"></div>
  <h4>GUARANTEED<br>SATISFACTION</h4><div class="rule"></div>
  <p>Join our community of satisfied customers who are already enjoying their custom above-ground pools. 10-Year Warranty!</p>
</article>
<article class="card" style="left:788px">
  <div class="photo" role="img" aria-label="Photo: vintage telephone" style="background:var(--photo-dark)"></div>
  <h4>CONTACT US<br>TODAY</h4><div class="rule"></div>
  <p>Contact us today to discover our range of customizable above-ground pools and get a tailored quote. Dive into infinite possibilities with Brisa Lagoon.</p>
</article>

<!-- footer -->
<footer class="site-footer">
  <div class="brand-footer">BRISA<br>LAGOON</div>
  <div class="social" aria-label="Social media links"><i></i><i></i><i></i><i></i></div>
  <div class="footer-col" style="left:446px">
    <h5>CONTACT US<br>BRISA LAGOON</h5>
    <p>Marco Velani<br>Rue des Tilleuls 27<br>1860 Aigle</p>
    <p style="margin-top:10px">Contact Us</p>
    <p style="display:flex;align-items:center;gap:10px"><svg width="16" height="16" viewBox="0 0 24 24"><path d="M6.6 10.8a15 15 0 006.6 6.6l2.2-2.2a1 1 0 011-.25 11 11 0 003.5.56 1 1 0 011 1V20a1 1 0 01-1 1A17 17 0 013 4a1 1 0 011-1h3.5a1 1 0 011 1 11 11 0 00.56 3.5 1 1 0 01-.25 1z" fill="#2d3436"/></svg>079 000 12 34</p>
  </div>
  <div class="footer-col" style="left:788px">
    <h5 style="margin-bottom:8px">SUBSCRIBE</h5>
    <p>Enter your email address to register to our<br>newsletter subscription</p>
    <div class="sub-form"><span>Enter e-mail address</span><b>Subscribe</b></div>
  </div>
  <div class="footer-rule"></div>
  <div class="copyright">© 2024 Brisa Lagoon. All rights reserved.</div>
</footer>

</body>
</html>
```